Structural Engineering Business Card

Brookvane Drafting does residential house plans for clients in Central Florida. Would like simple but elegant business card that is appropriate for a house plan engineering company. Prefer black business card with black/white them but open to other shades of blue. I uploaded a sample card that I came across that looked good but please come up with your own creative designs.

Contact Information for Business Card

Name, Title, Phone, Email, Address, website

```html
<!DOCTYPE html>
<html lang="en">
<head>
<meta charset="utf-8">
<title>Brookvane Drafting — Business Card</title>
<link href="https://fonts.googleapis.com/css2?family=Arimo:wght@400;700&display=swap" rel="stylesheet">
<style>
  :root {
    --page-bg: #2b2b2b;
    --card-bg: #1c1c1c;
    --ink: #ffffff;
    --rule: #d9d9d9;
  }
  * { margin: 0; padding: 0; box-sizing: border-box; }
  html, body { width: 1200px; height: 1059px; overflow: hidden; }
  body {
    background: var(--page-bg);
    font-family: "Arimo", Arial, sans-serif;
    color: var(--ink);
    position: relative;
  }
  .card {
    position: absolute;
    background: var(--card-bg);
    border-radius: 14px;
  }
  .card--front { left: 257px; top: 89px; width: 687px; height: 390px; }
  .card--back  { left: 254px; top: 547px; width: 693px; height: 394px; }

  .brand {
    position: absolute;
    display: flex;
    align-items: center;
    gap: 10px;
    font-weight: 700;
    letter-spacing: 0.5px;
    white-space: nowrap;
  }
  .brand__square { background: var(--ink); flex: none; }
  .card--front .brand { right: 35px; top: 70px; font-size: 32px; }
  .card--front .brand__square { width: 22px; height: 22px; }
  .card--back .brand {
    left: 50%; top: 50%; transform: translate(-50%, -50%);
    font-size: 48px; gap: 14px;
  }
  .card--back .brand__square { width: 32px; height: 32px; }

  .person { position: absolute; left: 35px; top: 182px; }
  .person__name { font-weight: 700; font-size: 23px; letter-spacing: 0.6px; line-height: 1.2; }
  .person__title { font-size: 17px; line-height: 1.2; margin-top: 1px; }

  .rule {
    position: absolute; left: 35px; right: 35px; top: 250px;
    height: 1px; background: var(--rule);
  }

  .contacts { position: absolute; left: 35px; top: 270px; list-style: none; }
  .contacts li {
    display: flex; align-items: center; gap: 6px;
    font-size: 17px; height: 29px;
  }
  .contacts svg { width: 13px; height: 13px; fill: var(--ink); flex: none; }

  .address {
    position: absolute; right: 35px; top: 298px;
    font-size: 17px; line-height: 25px; text-align: right; font-style: normal;
  }
</style>
</head>
<body>
  <section class="card card--front" aria-label="Card front">
    <div class="brand"><span class="brand__square"></span>Brookvane Drafting</div>

    <div class="person">
      <div class="person__name">DANIEL WHITMORE</div>
      <div class="person__title">Founder/CEO</div>
    </div>

    <div class="rule"></div>

    <ul class="contacts">
      <li>
        <svg viewBox="0 0 16 16" aria-hidden="true"><path d="M1 6c0-2 3-4 7-4s7 2 7 4v1h-4V5.5C10 5 9 5 8 5s-2 0-3 .5V7H1z M3 8h10l1 6H2z"/></svg>
        555.214.3870
      </li>
      <li>
        <svg viewBox="0 0 16 16" aria-hidden="true"><path d="M1 3h14v1.5L8 9 1 4.5z M1 6.3 8 11l7-4.7V13H1z"/></svg>
        info@brookvane.com
      </li>
      <li>
        <svg viewBox="0 0 16 16" aria-hidden="true"><path d="M8 1a7 7 0 1 0 0 14A7 7 0 0 0 8 1zm0 1.5a5.5 5.5 0 0 1 0 11 5.5 5.5 0 0 1 0-11z M5 5l3 1 1 3-2 2-1-3-2-1z"/></svg>
        www.brookvane.com
      </li>
    </ul>

    <address class="address">
      1820 Harbor Ln Suite 310<br>
      Lakewood, FL 32801
    </address>
  </section>

  <section class="card card--back" aria-label="Card back">
    <div class="brand"><span class="brand__square"></span>Brookvane Drafting</div>
  </section>
</body>
</html>
```